Cat-products company needs smart, yet endearing, business card

We need a business card design for a new, but up-and-running, business based in Honolulu, Hawaii. The business is Purrnest Nook Co. Our first product is the most environmentally-friendly cat grass kit ever seen on the planet. Future products, currently in the R&D phase, will include a variety of exciting cat scratchers. We also do consulting work to help apartment-dwellers make their home more cat-friendly and, in the future, plan on doing full, custom installs of structure to create high walkways for cats.

Target Market(s)

Middle-aged, apartment-dwelling, middle-class workers who own 1 or more cats and who dote on them.

Industry/Entity Type

Pet Care

Contact Information for Business Card

A striking, professional, yet warm and friendly design is what we're after.

Font styles to use
Serif
Sans Serif
Other font styles liked:
• Comfortaa

Colors

Designer to choose colors to be used in the design.

Requirements
Must have
• The company logo: (see attachment)
• The company name: Purrnest Nook Co
• The web address: www.purrnestnookco.com
• Email: support@purrnestnookco.com
• Phone: +1 (808) 571 6023
• Update (Fri Jun 30 3017 7:45pm Hawaii Time) I would like, is possible, uploaded picture of the cat grass kit on the back of the card with some text along the lines of: Purrnest Nook Co - Maker Of The Leafiest Feline Sprout Set Yet
Nice to have
• A cat picture, cartoon, real or silhouette that illustrates cats in action and/or relaxing; ie using the apartment space to live, play and relax in and being well-contented.
• Most of the website is done in the font: Comfortaa. It might be nice to continue using this for brand consistency.
Should not have
• Hard-to-read fonts.

```html
<!DOCTYPE html>
<html lang="en">
<head>
<meta charset="utf-8">
<title>Purrnest Nook Co — Business Card</title>
<link rel="stylesheet" href="https://fonts.googleapis.com/css2?family=Comfortaa:wght@400;700&display=swap">
<style>
  :root {
    --brown: #553129;
    --yellow: #f7b318;
    --white: #ffffff;
    --rule: #c9b5ad;
    --backdrop: #2a2a2c;
    --photo-wall: #eeeae4;
    --photo-door: #dcd8d2;
    --photo-sisal: #d9c9a3;
    --photo-wood: #a87548;
    --photo-ginger: #d08a44;
  }
  * { box-sizing: border-box; margin: 0; padding: 0; }
  html, body { width: 1200px; height: 1076px; overflow: hidden; }
  body {
    background: var(--backdrop);
    font-family: "Comfortaa", sans-serif;
    position: relative;
  }
  .card {
    position: absolute;
    left: 180px;
    width: 840px;
    height: 480px;
    background: var(--white);
    overflow: hidden;
    box-shadow: 0 10px 30px rgba(0,0,0,.45);
  }
  .card--front { top: 38px; }
  .card--back { top: 558px; }

  /* Shared brand lockup */
  .brand {
    position: absolute;
    display: flex; flex-direction: column; align-items: center;
  }
  .brand__mark {
    background: var(--brown);
    border-radius: 50%;
  }
  .brand__name {
    color: var(--yellow);
    font-weight: 700;
    text-align: center;
    line-height: 1.05;
    letter-spacing: .5px;
  }

  /* Front */
  .brand-area { position: absolute; left: 0; top: 0; width: 440px; height: 480px; }
  .brand-area .rule {
    position: absolute; left: 90px; width: 270px; height: 1px; background: var(--rule);
  }
  .brand-area .rule--top { top: 58px; }
  .brand-area .rule--bottom { top: 420px; }
  .brand-area .brand { left: 0; right: 0; top: 128px; }
  .brand-area .brand__mark { width: 84px; height: 84px; margin-bottom: 18px; }
  .brand-area .brand__name { font-size: 42px; }

  .contact-panel {
    position: absolute; left: 460px; top: 56px; width: 348px; height: 356px;
    background: var(--brown); color: var(--white);
    padding: 50px 24px 0 28px;
  }
  .contact-panel__name {
    color: var(--yellow); font-weight: 700; font-size: 28px; line-height: 1;
  }
  .contact-panel__role { font-size: 18px; margin-top: 4px; }
  .contact-list { list-style: none; margin-top: 44px; }
  .contact-list li {
    display: flex; align-items: center; gap: 10px;
    font-size: 16px; margin-bottom: 10px; white-space: nowrap;
  }
  .contact-list svg { flex: none; }
  .contact-panel__web {
    color: var(--yellow); font-weight: 700; font-size: 19px; margin-top: 18px;
    white-space: nowrap;
  }

  /* Back */
  .photo {
    position: absolute; left: 0; top: 0; width: 560px; height: 480px;
    clip-path: polygon(0 0, 78% 0, 100% 100%, 0 100%);
    background:
      linear-gradient(180deg, transparent 70%, rgba(168,117,72,.55) 100%),
      linear-gradient(95deg,
        var(--photo-wall) 0%, var(--photo-door) 18%,
        var(--photo-sisal) 32%, var(--photo-door) 44%,
        var(--photo-ginger) 56%, var(--photo-sisal) 72%,
        var(--photo-wall) 100%);
  }
  .card--back .brand { left: 520px; right: 0; top: 70px; }
  .card--back .brand__mark { width: 150px; height: 150px; margin-bottom: 20px; }
  .card--back .brand__name { font-size: 52px; }
  .social {
    position: absolute; left: 520px; right: 0; top: 372px;
    display: flex; justify-content: center; gap: 22px;
  }
  .social__item {
    width: 54px; height: 54px; border-radius: 6px; background: var(--brown);
  }
</style>
</head>
<body>
  <section class="card card--front">
    <div class="brand-area">
      <div class="rule rule--top"></div>
      <div class="brand">
        <div class="brand__mark"></div>
        <p class="brand__name">Purrnest<br>Nook Co</p>
      </div>
      <div class="rule rule--bottom"></div>
    </div>
    <div class="contact-panel">
      <p class="contact-panel__name">Employee Name</p>
      <p class="contact-panel__role">Manager</p>
      <ul class="contact-list">
        <li>
          <svg width="24" height="24" viewBox="0 0 24 24" aria-hidden="true">
            <circle cx="12" cy="12" r="11" fill="none" stroke="#f7b318" stroke-width="1.6"/>
            <path d="M8 7.5c.6-.6 1.4-.6 1.8 0l1 1.5c.3.5.2 1-.2 1.4l-.6.5c.6 1.3 1.6 2.3 2.9 2.9l.5-.6c.4-.4.9-.5 1.4-.2l1.5 1c.6.4.6 1.2 0 1.8l-.7.7c-.7.7-4 .1-6.3-2.2S6.6 8.9 7.3 8.2z" fill="#f7b318"/>
          </svg>
          +1 (808) 571 6023
        </li>
        <li>
          <svg width="24" height="24" viewBox="0 0 24 24" aria-hidden="true">
            <circle cx="12" cy="12" r="11" fill="none" stroke="#f7b318" stroke-width="1.6"/>
            <rect x="6.5" y="8" width="11" height="8" rx="1" fill="#f7b318"/>
            <path d="M7 8.8l5 3.6 5-3.6" fill="none" stroke="#553129" stroke-width="1.1"/>
          </svg>
          support@purrnestnookco.com
        </li>
      </ul>
      <p class="contact-panel__web">www.purrnestnookco.com</p>
    </div>
  </section>

  <section class="card card--back">
    <div class="photo" role="img" aria-label="Photo of cats on a wall-mounted cat tree beside a white door, and a ginger cat stretching up a sisal scratching post"></div>
    <div class="brand">
      <div class="brand__mark"></div>
      <p class="brand__name">Purrnest<br>Nook Co</p>
    </div>
    <div class="social" aria-label="Social media links">
      <span class="social__item"></span>
      <span class="social__item"></span>
      <span class="social__item"></span>
      <span class="social__item"></span>
    </div>
  </section>
</body>
</html>
```